New Business Card Design Project

Use the flyer uploaded and website www.brightoakbuilders.com for inspiration.
List Our Services on Backside of business cards
Marcus Delling
Harborline Builders Inc.
Licensed General Contractors
858-471-6093

Contact Information for Business Card

Use the flyer uploaded and website www.brightoakbuilders.com for inspiration. List Our Services on Backside of business cards Marcus Delling Harborline Builders Inc. Licensed General Contractors 858-471-6093

```html
<!DOCTYPE html>
<html lang="en">
<head>
<meta charset="utf-8">
<title>Harborline Builders – Business Card</title>
<link rel="stylesheet" href="https://fonts.googleapis.com/css2?family=Cormorant+Garamond:wght@500&family=Lato:wght@400;700;900&display=swap">
<style>
  :root {
    --stage: #1c1c1e;
    --card-dark: #111113;
    --card-light: #ffffff;
    --silver: #e4e4e6;
    --blue: #3a86d4;
    --red: #e8333a;
    --ink: #2a2a2e;
  }
  * { box-sizing: border-box; margin: 0; padding: 0; }
  html, body { width: 1200px; height: 939px; overflow: hidden; }
  body { background: var(--stage); font-family: "Lato", sans-serif; position: relative; }

  .card {
    position: absolute;
    width: 500px; height: 286px;
    border-radius: 16px;
    overflow: hidden;
    box-shadow: 0 12px 30px rgba(0,0,0,.45);
  }

  /* Services side */
  .card--services { left: 80px; top: 150px; background: var(--card-dark); color: var(--silver); text-align: center; }
  .card--services .brand-name { margin-top: 104px; font-size: 36px; }
  .services { margin-top: 34px; font-size: 12px; letter-spacing: 1px; line-height: 22px; text-transform: uppercase; }

  .brand-name {
    font-family: "Cormorant Garamond", serif;
    font-weight: 500;
    color: var(--silver);
    text-transform: uppercase;
    letter-spacing: 1px;
  }

  /* Contact side */
  .card--contact { left: 620px; top: 500px; background: var(--card-light); }
  .contact-band { position: absolute; left: 0; top: 0; width: 100%; height: 150px; background: var(--card-dark); }
  .contact-band .brand-name { position: absolute; right: 34px; top: 86px; font-size: 24px; }
  .frame { position: absolute; inset: 0; }

  .person { position: absolute; right: 44px; top: 178px; text-align: right; }
  .person-name { font-weight: 900; color: var(--blue); font-size: 26px; text-transform: uppercase; letter-spacing: .5px; }
  .person-title { color: var(--red); font-size: 14px; margin-top: 2px; }

  .contact-list { position: absolute; left: 52px; top: 172px; list-style: none; color: var(--ink); font-size: 12.5px; }
  .contact-list li { display: flex; align-items: center; gap: 8px; height: 22px; }
  .contact-list svg { width: 12px; height: 12px; fill: var(--blue); flex: none; }
  .contact-list strong { font-weight: 700; font-size: 14px; }
</style>
</head>
<body>

<section class="card card--services">
  <div class="brand-name">Harborline Builders</div>
  <p class="services">Painting | Flooring | Kitchens | Bathrooms<br>Energy Efficient Upgrades | Custom Renovations</p>
</section>

<section class="card card--contact">
  <div class="contact-band">
    <div class="brand-name">Harborline Builders</div>
  </div>
  <svg class="frame" viewBox="0 0 500 286" aria-hidden="true">
    <polyline points="36,286 36,142 470,142 470,166" fill="none" stroke="var(--blue)" stroke-width="4"/>
  </svg>

  <ul class="contact-list">
    <li><svg viewBox="0 0 12 12"><path d="M6 0a4 4 0 0 0-4 4c0 3 4 8 4 8s4-5 4-8a4 4 0 0 0-4-4zm0 5.6A1.6 1.6 0 1 1 6 2.4a1.6 1.6 0 0 1 0 3.2z"/></svg>Harborline Builders Inc.</li>
    <li><svg viewBox="0 0 12 12"><path d="M2.5 0 4.6 2.6 3.4 4.2a7 7 0 0 0 4.4 4.4l1.6-1.2L12 9.5 10.4 12C5 11.5.5 7 0 1.6z"/></svg><span><strong>858-471-6093</strong> Call/Text</span></li>
    <li><svg viewBox="0 0 12 12"><path d="M0 2h12v8H0zm1 1 5 4 5-4z"/></svg>info@brightoakbuilders.com</li>
    <li><svg viewBox="0 0 12 12"><path d="M6 0a6 6 0 1 0 0 12A6 6 0 0 0 6 0zm0 1.2c.8 1 1.3 2.3 1.4 3.8H4.6C4.7 3.5 5.2 2.2 6 1.2zM4.6 6h2.8c-.1 1.5-.6 2.8-1.4 3.8-.8-1-1.3-2.3-1.4-3.8zM1.3 6h2.3c.1 1.3.4 2.5 1 3.5A4.8 4.8 0 0 1 1.3 6zm7.1 0h2.3a4.8 4.8 0 0 1-3.3 3.5c.6-1 .9-2.2 1-3.5zm0-1c-.1-1.3-.4-2.5-1-3.5A4.8 4.8 0 0 1 10.7 5zM3.6 5H1.3a4.8 4.8 0 0 1 3.3-3.5c-.6 1-.9 2.2-1 3.5z"/></svg>www.brightoakbuilders.com</li>
  </ul>

  <div class="person">
    <div class="person-name">Marcus Delling</div>
    <div class="person-title">Licensed General Contractors</div>
  </div>
</section>

</body>
</html>
```